Brisk Fixwell business card

I need business card for my business, I think you have all my details.six months ago I design with you car wrap design. We would like to design both side of the card. On front of card we would like logo , Name and our contact details.
At the back we are looking to mentioned our services.
The name will be:
Faridoullan Mestor
Managing Director
Ph:07952338417
Email:info@brisk-fixwell.com
Web:www.brisk-fixwell.com
So we have our logo, you don’t need to change the logo.
Please see the attachment.
Thanks

Target Market(s)

Home improvement

Industry/Entity Type

Home Improvement

Contact Information for Business Card

Company name: Brisk Fixwell
Name: Faridoullan Mestor
Position: Director
Ph:07952338417
Web: www.brisk-fixwell.com
Add: 42 Corvale Road
Hounslow
TW3 9KD
SECOND PERSON
Nizamuddel mestor
Position: Handyman
Ph: 07812 564037
Email: info@brisk-fixwell.com
Add: 18 Brackwin Lane Road
Hounslow
TW6 2LB

```html
<!DOCTYPE html>
<html lang="en">
<head>
<meta charset="utf-8">
<title>Brisk Fixwell – Business Card</title>
<link rel="stylesheet" href="https://fonts.googleapis.com/css2?family=Arimo:wght@400;700&display=swap">
<style>
  :root {
    --stage: #2a2a2c;
    --navy: #233a8a;
    --navy-deep: #1e3280;
    --red: #e31e2d;
    --grey: #9a9b9f;
    --ink: #3a3a3c;
    --white: #ffffff;
  }
  * { box-sizing: border-box; margin: 0; padding: 0; }
  html, body {
    width: 1200px; height: 1015px; overflow: hidden;
    background: var(--stage);
    font-family: "Arimo", Arial, sans-serif;
  }
  .card {
    position: absolute; left: 210px;
    width: 780px; height: 446px;
    overflow: hidden;
    box-shadow: 0 14px 30px rgba(0,0,0,.55);
  }
  /* ---------- back: services ---------- */
  .card--back { top: 40px; background: var(--navy); }
  .card--back .pattern-field {
    position: absolute; inset: 0;
    background: linear-gradient(135deg, #2a44a0 0%, var(--navy) 55%, var(--navy-deep) 100%);
  }
  .card--back .brand {
    position: absolute; top: 150px; left: 0; right: 0;
    text-align: center; color: var(--white);
    font-weight: 700; font-size: 40px; letter-spacing: 1px;
  }
  .services {
    position: absolute; left: 40px; right: 40px; bottom: 44px;
    display: flex; justify-content: space-between;
    list-style: none;
  }
  .services__col { display: flex; flex-direction: column; gap: 6px; }
  .services__item {
    color: var(--white); font-size: 22px; white-space: nowrap;
    display: flex; align-items: center; gap: 7px;
  }
  .services__item::before {
    content: ""; width: 8px; height: 8px; border-radius: 50%;
    background: var(--red); flex: none;
  }
  /* ---------- front: contact ---------- */
  .card--front { top: 529px; background: var(--white); }
  .card--front .brand {
    position: absolute; left: 60px; top: 180px;
    display: flex; align-items: center; gap: 14px;
    color: var(--navy); font-weight: 700; font-size: 42px;
  }
  .brand__mark { width: 26px; height: 26px; background: var(--red); }
  .contact { position: absolute; left: 440px; top: 62px; color: var(--ink); }
  .contact__name {
    color: var(--navy); font-weight: 700; font-size: 26px; letter-spacing: .3px;
  }
  .contact__role { font-size: 19px; color: #55565a; margin: 2px 0 18px; letter-spacing: .5px; }
  .contact__line {
    display: flex; align-items: center; gap: 10px;
    font-size: 19px; line-height: 1.45; white-space: nowrap;
  }
  .contact__line svg { width: 18px; height: 18px; fill: var(--navy); flex: none; }
  .contact__line .hl { color: var(--navy); }
  .contact__address { font-size: 19px; line-height: 1.35; margin: 8px 0 0 28px; }
  .bands { position: absolute; left: 0; right: 0; bottom: 0; height: 44px; }
  .band { position: absolute; bottom: 0; }
  .band--grey { left: 0; width: 238px; height: 14px; background: var(--grey); }
  .band--red { left: 244px; width: 258px; height: 26px; background: var(--red); }
  .band--navy { left: 508px; right: 0; height: 44px; background: var(--navy); }
</style>
</head>
<body>

<section class="card card--back" aria-label="Card back – services">
  <div class="pattern-field" role="img" aria-label="Blue background with a faint repeating emblem pattern"></div>
  <div class="brand">Brisk Fixwell</div>
  <ul class="services">
    <li class="services__col"><span class="services__item">Plumbing</span><span class="services__item">Carpentry</span></li>
    <li class="services__col"><span class="services__item">Decking</span><span class="services__item">Fence</span></li>
    <li class="services__col"><span class="services__item">Gutter</span><span class="services__item">Flooring</span></li>
    <li class="services__col"><span class="services__item">Plastering</span><span class="services__item">Tilling</span></li>
    <li class="services__col"><span class="services__item">Painting &amp; Decorating</span><span class="services__item">Gardening</span></li>
  </ul>
</section>

<section class="card card--front" aria-label="Card front – contact details">
  <div class="brand"><span class="brand__mark"></span>Brisk Fixwell</div>

  <div class="contact">
    <div class="contact__name">FARIDOULLAN MESTOR</div>
    <div class="contact__role">DIRECTOR</div>
    <div class="contact__line">
      <svg viewBox="0 0 24 24"><path d="M6.6 10.8a15.1 15.1 0 0 0 6.6 6.6l2.2-2.2c.3-.3.7-.4 1-.2 1.1.4 2.3.6 3.6.6.6 0 1 .4 1 1V20c0 .6-.4 1-1 1C10.6 21 3 13.4 3 4c0-.6.4-1 1-1h3.5c.6 0 1 .4 1 1 0 1.3.2 2.5.6 3.6.1.3 0 .7-.2 1z"/></svg>
      07952338417
    </div>
    <div class="contact__line">
      <svg viewBox="0 0 24 24"><path d="M2 5h20v14H2zm2 2v.4l8 5.2 8-5.2V7zm0 2.8V17h16V9.8l-8 5.2z"/></svg>
      info@brisk-fixwell.com
    </div>
    <div class="contact__line">
      <svg viewBox="0 0 24 24"><path d="M12 2a10 10 0 1 0 0 20 10 10 0 0 0 0-20zm6.9 6h-3a15 15 0 0 0-1.3-4A8 8 0 0 1 18.9 8zM12 4c.9 1.2 1.6 2.6 2 4h-4c.4-1.4 1.1-2.8 2-4zM4.3 14a8 8 0 0 1 0-4h3.4a16 16 0 0 0 0 4zm.8 2h3a15 15 0 0 0 1.3 4A8 8 0 0 1 5.1 16zm3-8h-3a8 8 0 0 1 4.3-4A15 15 0 0 0 8.1 8zM12 20c-.9-1.2-1.6-2.6-2-4h4c-.4 1.4-1.1 2.8-2 4zm2.3-6H9.7a14 14 0 0 1 0-4h4.6a14 14 0 0 1 0 4zm.3 6a15 15 0 0 0 1.3-4h3a8 8 0 0 1-4.3 4zm1.7-6a16 16 0 0 0 0-4h3.4a8 8 0 0 1 0 4z"/></svg>
      <span>www.<span class="hl">brisk-fixwell</span>.com</span>
    </div>
    <div class="contact__address">42 Corvale Road<br>Hounslow,TW3 9KD</div>
  </div>

  <div class="bands">
    <span class="band band--grey"></span>
    <span class="band band--red"></span>
    <span class="band band--navy"></span>
  </div>
</section>

</body>
</html>
```